design a construction company business card

Design business card around our logo. Card must have all the typical info: name, title, address, phone, email, business name, etc. Somewhere on the card I would like to see our motto "Grounded in trust... driven by dedication." Consider adding a splash of bright orange to the card to complement the blues and silvers/grays in the logo. We are open to metallic inks, textures, etc. We would like to see options on both light and dark backgrounds. The font in the logo is Euro Technic Extended Regular.

```html
<!DOCTYPE html>
<html lang="en">
<head>
<meta charset="utf-8">
<title>Kestrel Contracting, Inc. — Business Card</title>
<link href="https://fonts.googleapis.com/css2?family=Michroma&family=Montserrat:wght@700&display=swap" rel="stylesheet">
<style>
  :root {
    --backdrop: #4a4a4c;
    --card: #1f2022;
    --card-edge: #2a2b2e;
    --brand-blue: #2a78d6;
    --text-light: #d2d4d8;
  }
  * { margin: 0; padding: 0; box-sizing: border-box; }
  html, body { width: 1200px; height: 1000px; overflow: hidden; }
  body {
    background: var(--backdrop);
    position: relative;
    font-family: "Michroma", sans-serif;
  }
  .card {
    position: absolute;
    width: 700px;
    height: 400px;
    border-radius: 26px;
    background: linear-gradient(135deg, var(--card-edge), var(--card) 60%);
    overflow: hidden;
  }
  .card-front { left: 440px; top: 50px; }
  .card-back {
    left: 60px; top: 530px;
    border-bottom: 10px solid var(--brand-blue);
  }

  .brand {
    position: absolute;
    display: flex;
    align-items: center;
    gap: 16px;
  }
  .brand-mark {
    width: 18px; height: 18px;
    background: var(--brand-blue);
    flex: none;
  }
  .brand-name {
    font-family: "Michroma", sans-serif;
    font-weight: 400;
    color: var(--brand-blue);
    font-size: 26px;
    line-height: 1.35;
    letter-spacing: 2px;
    text-transform: uppercase;
  }

  .card-front .brand { left: 0; right: 0; top: 130px; justify-content: center; }
  .card-back .brand { left: 44px; top: 80px; }

  .motto {
    position: absolute; left: 0; right: 0; top: 300px;
    text-align: center;
    font-family: "Montserrat", sans-serif;
    font-weight: 700;
    font-size: 15px;
    letter-spacing: 1.5px;
    color: var(--brand-blue);
    text-transform: uppercase;
  }

  .contact {
    position: absolute; right: 40px; bottom: 30px;
    text-align: right;
    color: var(--text-light);
  }
  .contact-name { font-size: 24px; color: var(--brand-blue); letter-spacing: 1px; }
  .contact-title { font-size: 14px; margin: 6px 0 22px; }
  .contact-line { font-size: 14px; line-height: 25px; display: flex; justify-content: flex-end; align-items: center; gap: 10px; }
  .contact-line .accent { color: var(--brand-blue); }
  .icon { width: 14px; height: 14px; flex: none; }
  .icon-spacer { width: 14px; flex: none; }
</style>
</head>
<body>

  <section class="card card-front" aria-label="Card front">
    <div class="brand">
      <span class="brand-mark" aria-hidden="true"></span>
      <div class="brand-name">Kestrel<br>Contracting, Inc.</div>
    </div>
    <p class="motto">Grounded in trust... driven by dedication.</p>
  </section>

  <section class="card card-back" aria-label="Card back">
    <div class="brand">
      <span class="brand-mark" aria-hidden="true"></span>
      <div class="brand-name">Kestrel<br>Contracting, Inc.</div>
    </div>

    <div class="contact">
      <div class="contact-name">Marcus Hale</div>
      <div class="contact-title">Managing Director</div>
      <div class="contact-line">480 Harbor Avenue N.Y.<span class="icon-spacer"></span></div>
      <div class="contact-line">Brookvale AB T1R<span class="icon-spacer"></span></div>
      <div class="contact-line">555.014.2700
        <svg class="icon" viewBox="0 0 16 16" aria-hidden="true"><circle cx="8" cy="8" r="8" fill="var(--brand-blue)"/><path d="M5 4.5l1.6-.4 1 2-1 .8c.5 1.1 1.3 1.9 2.4 2.4l.8-1 2 1-.4 1.6C8 11 5 8 5 4.5z" fill="#1f2022"/></svg>
      </div>
      <div class="contact-line">marcus@kestrelbuild.com
        <svg class="icon" viewBox="0 0 16 16" aria-hidden="true"><circle cx="8" cy="8" r="8" fill="var(--brand-blue)"/><rect x="4" y="5" width="8" height="6" fill="#1f2022"/><path d="M4 5l4 3.2L12 5" stroke="var(--brand-blue)" stroke-width="1" fill="none"/></svg>
      </div>
      <div class="contact-line"><span>www.<span class="accent">kestrelbuild</span>.com</span>
        <svg class="icon" viewBox="0 0 16 16" aria-hidden="true"><circle cx="8" cy="8" r="8" fill="var(--brand-blue)"/><circle cx="8" cy="8" r="4.2" fill="none" stroke="#1f2022" stroke-width="1.2"/><path d="M3.8 8h8.4M8 3.8c-1.6 2.6-1.6 5.8 0 8.4M8 3.8c1.6 2.6 1.6 5.8 0 8.4" stroke="#1f2022" stroke-width="1" fill="none"/></svg>
      </div>
    </div>
  </section>

</body>
</html>
```